Business Cards for a law firm

Business cards for our law firm. Use our silhoette logo and OAK PARTNERS - check our website (www.oakpartners.example)

Contact Information for Business Card

our silhouette logo, OAK PARTNERS, 800-555-0147, Dorian Pemberton, dorian@oakpartners.example

Requirements
Must have
• our silhouette logo, OAK PARTNERS, 800-555-0147, Dorian Pemberton, dorian@oakpartners.example

```html
<!DOCTYPE html>
<html lang="en">
<head>
<meta charset="utf-8">
<title>Oak Partners – Business Cards</title>
<link href="https://fonts.googleapis.com/css2?family=Marcellus+SC&family=Arimo:wght@400&display=swap" rel="stylesheet">
<style>
  :root {
    --navy: #172f6b;
    --navy-soft: #2a4383;
    --gold: #f0a020;
    --white: #ffffff;
    --paper: #ffffff;
    --backdrop: #2b2522;
    --edge: #e79a14;
  }
  * { box-sizing: border-box; margin: 0; padding: 0; }
  html, body {
    width: 1200px; height: 716px; overflow: hidden;
    background: var(--backdrop);
  }
  .stage {
    position: relative; width: 1200px; height: 716px;
    display: flex; align-items: center; justify-content: center; gap: 40px;
  }
  .card {
    position: relative; width: 540px; height: 309px;
    border-radius: 22px; overflow: hidden;
    box-shadow: 0 3px 0 var(--edge), 0 14px 30px rgba(0,0,0,.55);
  }
  .card--front { background: var(--navy); }
  .card--back { background: var(--paper); }

  .brand {
    position: absolute; left: 44px; top: 46px;
    display: flex; align-items: center; gap: 10px;
    font-family: "Marcellus SC", serif; letter-spacing: 2px;
  }
  .brand__mark { width: 14px; height: 14px; border-radius: 50%; background: var(--white); }
  .brand__name { color: var(--white); font-size: 20px; }

  .holder { position: absolute; left: 44px; top: 118px; }
  .holder__rule { width: 22px; height: 1px; background: var(--gold); margin-bottom: 10px; }
  .holder__name {
    font-family: "Marcellus SC", serif; color: var(--gold);
    font-size: 21px; letter-spacing: 1px;
  }

  .contacts {
    position: absolute; left: 44px; top: 178px; list-style: none;
    font-family: "Arimo", sans-serif; font-size: 12.5px; color: var(--white);
  }
  .contacts li { display: flex; align-items: center; gap: 9px; height: 19px; }
  .contacts svg { width: 11px; height: 11px; fill: var(--gold); flex: none; }

  .figure {
    position: absolute; border-radius: 60px 60px 6px 6px;
  }
  .card--front .figure {
    left: 360px; top: 48px; width: 110px; height: 240px;
    background: linear-gradient(180deg, rgba(255,255,255,.85), rgba(255,255,255,.7));
  }
  .card--back .figure {
    left: 60px; top: 48px; width: 120px; height: 238px;
    background: linear-gradient(180deg, var(--navy-soft), var(--navy));
  }

  .wordmark {
    position: absolute; right: 40px; bottom: 52px;
    font-family: "Marcellus SC", serif; color: var(--navy);
    font-size: 36px; letter-spacing: 4px;
  }
</style>
</head>
<body>
<main class="stage">
  <section class="card card--front">
    <div class="brand">
      <span class="brand__mark"></span>
      <span class="brand__name">OAK PARTNERS</span>
    </div>
    <div class="holder">
      <div class="holder__rule"></div>
      <div class="holder__name">Dorian Pemberton</div>
    </div>
    <ul class="contacts">
      <li>
        <svg viewBox="0 0 24 24"><path d="M6.6 10.8a15.1 15.1 0 0 0 6.6 6.6l2.2-2.2a1 1 0 0 1 1-.25 11.4 11.4 0 0 0 3.6.57 1 1 0 0 1 1 1V20a1 1 0 0 1-1 1A17 17 0 0 1 3 4a1 1 0 0 1 1-1h3.5a1 1 0 0 1 1 1c0 1.25.2 2.45.57 3.6a1 1 0 0 1-.25 1z"/></svg>
        800-555-0147
      </li>
      <li>
        <svg viewBox="0 0 24 24"><path d="M2 5h20v14H2z M2 5l10 8 10-8" fill="none" stroke="#f0a020" stroke-width="2.4"/></svg>
        dorian@oakpartners.example
      </li>
      <li>
        <svg viewBox="0 0 24 24"><circle cx="12" cy="12" r="9" fill="none" stroke="#f0a020" stroke-width="2.4"/><path d="M3 12h18M12 3c3 3 3 15 0 18M12 3c-3 3-3 15 0 18" fill="none" stroke="#f0a020" stroke-width="1.6"/></svg>
        www.oakpartners.example
      </li>
    </ul>
    <div class="figure" role="img" aria-label="White silhouette of a standing man in a suit"></div>
  </section>

  <section class="card card--back">
    <div class="figure" role="img" aria-label="Navy silhouette of a standing man in a suit"></div>
    <div class="wordmark">OAK PARTNERS</div>
  </section>
</main>
</body>
</html>
```